New business stationairy

I need paper with header and footer and business cards.
I am a Ltd Company and my main field of expertise is QA/QC inspection in the Oil and Gas Industry. I will need all contact detail inserted and a footer with registration number and bank details etc

```html
<!DOCTYPE html>
<html lang="en">
<head>
<meta charset="utf-8">
<title>Harlow Inspection Services – Stationery</title>
<link rel="stylesheet" href="https://fonts.googleapis.com/css2?family=Oswald:wght@500&family=Questrial&display=swap">
<style>
  :root {
    --navy: #2c2a68;
    --gold: #a8832f;
    --paper: #ffffff;
    --backdrop: #e9e7e6;
    --ink-soft: #5a5a66;
  }
  * { box-sizing: border-box; margin: 0; padding: 0; }
  html, body { width: 1200px; height: 843px; overflow: hidden; }
  body {
    background: var(--backdrop);
    position: relative;
    font-family: "Questrial", Arial, sans-serif;
  }
  address { font-style: normal; }

  .brand-name {
    font-family: "Oswald", "Arial Narrow", sans-serif;
    font-weight: 500;
    text-transform: uppercase;
    line-height: 1.02;
    color: var(--navy);
    display: flex;
    align-items: center;
    gap: 8px;
    white-space: nowrap;
  }
  .brand-name .brand-square {
    background: var(--gold);
    flex: none;
  }
  .brand-name.on-dark { color: #ffffff; }

  /* Letterhead */
  .letterhead {
    position: absolute;
    left: 410px; top: 70px;
    width: 480px; height: 679px;
    background: var(--paper);
    box-shadow: 0 2px 6px rgba(0,0,0,.12);
    overflow: hidden;
  }
  .letterhead .brand-name { position: absolute; left: 36px; top: 100px; font-size: 14px; }
  .letterhead .brand-square { width: 22px; height: 22px; }
  .letterhead-contact {
    position: absolute; right: 34px; top: 36px;
    text-align: right; font-size: 7.5px; line-height: 1.6;
    color: var(--ink-soft);
  }
  .letterhead-contact .company { text-transform: uppercase; letter-spacing: .3px; }
  .letterhead-footer { position: absolute; left: 0; bottom: 0; width: 100%; height: 125px; }

  /* Business cards */
  .card {
    position: absolute;
    width: 340px; height: 195px;
    box-shadow: 0 2px 6px rgba(0,0,0,.14);
    overflow: hidden;
  }
  .card-front { left: 30px; top: 210px; background: var(--navy); }
  .card-back { left: 30px; top: 460px; background: var(--paper); }
  .card-front .brand-name {
    position: absolute; left: 0; right: 0; top: 52px;
    justify-content: center; font-size: 14px;
  }
  .card-front .brand-square { width: 20px; height: 20px; }
  .card-front .card-address {
    position: absolute; left: 0; right: 0; top: 86px;
    text-align: center; color: #ffffff; font-size: 8.5px; line-height: 1.6;
  }
  .card-swoosh { position: absolute; left: 0; bottom: 0; width: 100%; }
  .card-back .brand-name { position: absolute; left: 30px; top: 26px; font-size: 13px; }
  .card-back .brand-square { width: 20px; height: 20px; }
  .card-person {
    position: absolute; right: 24px; top: 116px; text-align: right;
  }
  .card-person .person-name {
    color: var(--gold); font-size: 12px; text-transform: uppercase; letter-spacing: .6px;
  }
  .card-person .person-role { color: #ffffff; font-size: 9px; margin-top: 2px; }
  .card-contacts {
    position: absolute; left: 28px; top: 140px;
    list-style: none; color: #ffffff; font-size: 8.5px; line-height: 1.5;
  }
  .card-contacts li { display: flex; align-items: center; gap: 6px; }
  .card-contacts svg { width: 9px; height: 9px; }

  /* Logo variants */
  .logo-primary { position: absolute; left: 925px; top: 64px; font-size: 17px; }
  .logo-primary .brand-square { width: 40px; height: 40px; }
  .logo-line {
    position: absolute; left: 915px; top: 742px; font-size: 8px;
    flex-direction: column; align-items: flex-start; gap: 5px;
  }
  .logo-line .brand-square { width: 26px; height: 26px; }
  .logo-stacked { position: absolute; left: 1065px; top: 745px; font-size: 9.5px; }
  .logo-stacked .brand-square { width: 26px; height: 26px; }
</style>
</head>
<body>

<section class="letterhead" aria-label="Letterhead">
  <div class="brand-name"><span class="brand-square"></span><span>Harlow<br>Inspection<br>Services</span></div>
  <address class="letterhead-contact">
    <div class="company">Harlow Inspection Services Ltd</div>
    <div>Oak House, Mill Road, Ashford</div>
    <div>Bramley Cross, Dorset, DT4 1AB</div>
    <div>+07700 900123 &nbsp; info@harlowinspect.co.uk</div>
  </address>
  <svg class="letterhead-footer" viewBox="0 0 480 125" preserveAspectRatio="none" aria-hidden="true">
    <path d="M0 125 L0 100 C175 96 375 68 480 6 L480 125 Z" fill="var(--navy)"/>
    <path d="M0 90 C180 84 345 58 450 10" fill="none" stroke="var(--gold)" stroke-width="3"/>
  </svg>
</section>

<section class="card card-front" aria-label="Business card front">
  <div class="brand-name on-dark"><span class="brand-square"></span><span>Harlow Inspection Services</span></div>
  <address class="card-address">
    Oak House, Mill Road, Ashford<br>Bramley Cross, Dorset, DT4 1AB
  </address>
  <svg class="card-swoosh" viewBox="0 0 340 60" aria-hidden="true">
    <path d="M0 42 C115 40 240 28 340 0 L340 10 C240 36 115 48 0 50 Z" fill="var(--gold)"/>
    <path d="M0 56 C115 54 240 44 340 22 L340 28 C240 48 115 58 0 60 Z" fill="var(--gold)"/>
  </svg>
</section>

<section class="card card-back" aria-label="Business card back">
  <div class="brand-name"><span class="brand-square"></span><span>Harlow<br>Inspection<br>Services</span></div>
  <svg class="card-swoosh" viewBox="0 0 340 110" aria-hidden="true">
    <path d="M0 30 C115 24 240 12 340 0 L340 110 L0 110 Z" fill="var(--navy)"/>
    <path d="M0 24 C115 18 240 6 320 -4" fill="none" stroke="var(--gold)" stroke-width="2.5"/>
    <path d="M40 29 L46 36 L52 29 Z" fill="var(--paper)"/>
  </svg>
  <div class="card-person">
    <div class="person-name">Dana Whitmore</div>
    <div class="person-role">Managing Director</div>
  </div>
  <ul class="card-contacts">
    <li><svg viewBox="0 0 10 10"><circle cx="5" cy="5" r="4.2" fill="none" stroke="#fff"/><path d="M3.3 3 L4.3 3 L4.6 4.3 L4 4.8 C4.4 5.6 4.9 6 5.5 6.3 L6 5.7 L7.1 6 L7.1 7 C5 7 3.2 5.2 3.3 3 Z" fill="#fff"/></svg>+07700 900123</li>
    <li><svg viewBox="0 0 10 10"><circle cx="5" cy="5" r="4.2" fill="none" stroke="#fff"/><rect x="3.5" y="2.6" width="3" height="4.8" rx=".5" fill="#fff"/></svg>+07700 900124</li>
    <li><svg viewBox="0 0 10 10"><circle cx="5" cy="5" r="4.2" fill="none" stroke="#fff"/><rect x="2.8" y="3.5" width="4.4" height="3" fill="none" stroke="#fff" stroke-width=".8"/><path d="M2.8 3.5 L5 5.2 L7.2 3.5" fill="none" stroke="#fff" stroke-width=".8"/></svg>info@harlowinspect.co.uk</li>
  </ul>
</section>

<div class="brand-name logo-primary" aria-label="Primary brand lockup"><span>Harlow<br>Inspection<br>Services</span><span class="brand-square"></span></div>
<div class="brand-name logo-line" aria-label="Compact brand lockup"><span class="brand-square"></span><span>Harlow Inspection Services</span></div>
<div class="brand-name logo-stacked" aria-label="Stacked brand lockup"><span class="brand-square"></span><span>Harlow<br>Inspection<br>Services</span></div>

</body>
</html>
```